Dunmore Roofing

Want a professional looking business card

Industry/Entity Type

Business

Contact Information for Business Card

Paul Dunmore ( Owner) paul@dunmoreroofing-example.com, www.dunmoreroofing-example.com, Adress: 4172 Township road 43 Larkfield,ON K9X4T2

```html
<!DOCTYPE html>
<html lang="en">
<head>
<meta charset="utf-8">
<title>Dunmore Roofing – Business Card</title>
<link href="https://fonts.googleapis.com/css2?family=Exo+2:wght@400;600;800&display=swap" rel="stylesheet">
<style>
  :root {
    --backdrop: #111111;
    --card-dark: #1b1b1d;
    --card-light: #ffffff;
    --brand-blue: #24488f;
    --brand-blue-deep: #1f4189;
    --swoosh-gray: #8d8f94;
    --text-gray: #5b5d62;
    --text-white: #ffffff;
  }
  * { margin: 0; padding: 0; box-sizing: border-box; }
  html, body {
    width: 1200px; height: 1000px; overflow: hidden;
    background: var(--backdrop);
    font-family: "Exo 2", sans-serif;
  }
  .canvas { position: relative; width: 1200px; height: 1000px; }
  .card {
    position: absolute; width: 520px; height: 300px;
    border-radius: 22px; overflow: hidden;
  }
  .card--front { left: 60px; top: 230px; background: var(--card-dark); }
  .card--back { left: 620px; top: 470px; background: var(--card-light); }

  .wordmark {
    display: flex; align-items: center; gap: 10px;
    color: var(--brand-blue); font-weight: 800;
    text-transform: uppercase; letter-spacing: 1px; line-height: 1;
    white-space: nowrap;
  }
  .wordmark__mark { width: 14px; height: 14px; background: var(--brand-blue); flex: none; }
  .card--front .wordmark {
    position: absolute; left: 0; right: 0; top: 50%;
    transform: translateY(-50%); justify-content: center; font-size: 34px;
  }

  .wave { position: absolute; inset: 0; width: 520px; height: 300px; }
  .holder { position: absolute; left: 30px; top: 34px; }
  .holder__name { color: var(--brand-blue); font-weight: 600; font-size: 21px; line-height: 1.05; }
  .holder__role { color: var(--text-gray); font-size: 15px; }
  .card--back .wordmark {
    position: absolute; right: 28px; top: 118px; font-size: 24px;
  }
  .online {
    position: absolute; left: 24px; top: 196px;
    color: var(--text-white); font-size: 13.5px; line-height: 1.45;
  }
  .address {
    position: absolute; right: 28px; bottom: 16px; text-align: right;
    color: var(--text-white); font-size: 15px; line-height: 1.4;
    font-style: normal;
  }
</style>
</head>
<body>
<main class="canvas">
  <section class="card card--front" aria-label="Card front">
    <div class="wordmark"><span class="wordmark__mark"></span>Dunmore Roofing</div>
  </section>

  <section class="card card--back" aria-label="Card back">
    <svg class="wave" viewBox="0 0 520 300" aria-hidden="true">
      <path fill="var(--swoosh-gray)" d="M0,128 C140,98 230,160 340,202 C240,172 130,118 0,142 Z"/>
      <path fill="var(--brand-blue-deep)" d="M0,146 C140,122 220,182 300,205 C380,228 450,226 520,214 L520,300 L0,300 Z"/>
      <path fill="var(--brand-blue)" d="M250,188 C310,210 360,215 420,206 C360,220 300,214 250,188 Z"/>
    </svg>
    <div class="holder">
      <div class="holder__name">Paul Dunmore</div>
      <div class="holder__role">Owner</div>
    </div>
    <div class="wordmark"><span class="wordmark__mark"></span>Dunmore Roofing</div>
    <div class="online">
      <div>paul@dunmoreroofing-example.com</div>
      <div>www.dunmoreroofing-example.com</div>
    </div>
    <address class="address">
      <div>4172 Township road 43,</div>
      <div>Larkfield, ON K9X4T2</div>
    </address>
  </section>
</main>
</body>
</html>
```